Bright and beautiful business card for a coach

I'm a personal and business coach based in Perth, Australia. I need a business card that whilst subtle and elegant, will stand out and appeal on a table full of cards.

My business name is Fern Mentoring and the business card must represent the warmth and brightness implied in the name, without being gimmicky. It must have a warmth and appeal and be easy to read.

I prefer clean, minimalist designs.

It must align with the feel of my website and socials: https://www.fernmentoring-example.com.au/
https://www.instagram.com/fernmentoringau/
https://www.facebook.com/fernmentoringau
Updates

Hi Designers Thank you so much for taking the time to submit designs. I wonder if I could have explained myself a little better. Most of the designs that have been submitted look rather formal and many have quite corporate looking embellishments on them (to my eye). I would like softer, warmer, more organic. I’m open to people playing about and being more abstract, using softer embellishments (e.g the line drawing flowers and grasses I’ve used in my socials) incorporating other colours from my palette or like the social icons in my email signature (in PDF), perhaps playing with size/oversize, playing with the bleed. Please don’t be constrained by what I’ve already done, it merely needs to compliment. I’m sorry if I’m not using the right words or have led you astray. I’m no designer, but I’ve done my website, socials, email signature etc all myself (my logo was a design contest) and I was really hoping for my business card to be something more creative than I could have made with a template. Reminder: No black cards/sides please. Thank you 😊

Target Market(s)

Individuals, most likely but not all female. Creative thinkers. Likely professionals.

Industry/Entity Type

Business & Personal Coach

Contact Information for Business Card

(Fern Mentoring Logo) Name: Greta Pellham; Title: Business & Personal Coach; Phone number: +61 (0)458 913307; Email: greta@fernmentoring-example.com.au; Website: https://fernmentoring-example.com.au; Social icons for Facebook, Instagram & LinkedIn: @fernmentoringAU. Optional strapline: "A thinking partner to help you cut through the noise"

Font styles to use
Sans Serif

Colors
00AB8E
00BBA5
67D7C9
C6EFE9
E9F9F6
59FF00
82FF00
B8FF75
E3FFCB
F4FFEA
FFC000
F8CF3A
FAE287
FDF2CF
FEFAEE

Requirements
Must have
• Must align with feel of my website and socials. Must have a pop of #FFC000 (possibly whole of one side, or at least a block). Bright or white background. Easy to read.
Nice to have
• Possibly incorporate the sunshine/grass picture I have used in website and socials - will upload.
Should not have
• Must not be black or dark. Not impersonal or corporate looking.

```html
<!DOCTYPE html>
<html lang="en">
<head>
<meta charset="utf-8">
<title>Fern Mentoring – Business Card</title>
<link href="https://fonts.googleapis.com/css2?family=Lato:wght@400;700&family=Sacramento&display=swap" rel="stylesheet">
<style>
  :root {
    --sun: #FFC000;
    --sun-soft: #FAE287;
    --sun-pale: #FEFAEE;
    --ink: #8a8a8a;
    --ink-dark: #6f6f6f;
    --card: #ffffff;
    --stage: #b0b0b0;
  }
  * { box-sizing: border-box; margin: 0; padding: 0; }
  html, body { width: 1200px; height: 900px; overflow: hidden; }
  body {
    background: var(--stage);
    font-family: "Lato", sans-serif;
    position: relative;
  }
  .card {
    position: absolute;
    top: 135px;
    width: 360px;
    height: 630px;
    background: var(--card);
    overflow: hidden;
  }
  .card--front { left: 200px; }
  .card--back { left: 640px; }

  /* Front */
  .brand-disc {
    position: absolute;
    left: 50px; top: 185px;
    width: 260px; height: 260px;
    border-radius: 50%;
    background: var(--sun);
  }
  .brand-name {
    position: absolute;
    left: 0; right: 0; top: 295px;
    text-align: center;
    font-family: "Lato", sans-serif;
    font-weight: 700;
    font-size: 28px;
    letter-spacing: 2px;
    color: var(--card);
  }

  /* Back */
  .ray-field {
    position: absolute;
    left: -120px; top: 150px;
    width: 300px; height: 420px;
    border-radius: 50%;
    background: radial-gradient(circle at 30% 50%, var(--sun-soft) 0%, var(--sun-pale) 55%, rgba(255,255,255,0) 72%);
  }
  .contact {
    position: absolute;
    right: 26px; top: 34px;
    text-align: right;
  }
  .contact__name {
    font-family: "Sacramento", cursive;
    font-size: 50px;
    line-height: 1;
    color: var(--sun);
  }
  .contact__title {
    font-size: 13px;
    color: var(--ink-dark);
    letter-spacing: .3px;
    margin-top: 2px;
    padding-bottom: 7px;
    border-bottom: 1.5px solid var(--sun);
  }
  .contact__list { list-style: none; margin-top: 7px; }
  .contact__item {
    display: flex;
    align-items: center;
    justify-content: flex-end;
    gap: 6px;
    font-size: 11.5px;
    color: var(--ink-dark);
    line-height: 1.6;
  }
  .contact__icon { width: 11px; height: 11px; flex: none; }
  .strapline {
    position: absolute;
    right: 40px; top: 235px;
    width: 190px;
    text-align: center;
    font-family: "Sacramento", cursive;
    font-size: 34px;
    line-height: 1.15;
    color: var(--ink);
  }
  .social {
    position: absolute;
    right: 26px; bottom: 28px;
    display: flex;
    align-items: center;
    gap: 8px;
    font-size: 15px;
    color: var(--ink-dark);
  }
  .social__mark {
    width: 16px; height: 16px;
    background: var(--sun);
    border-radius: 3px;
  }
</style>
</head>
<body>

  <section class="card card--front" aria-label="Card front">
    <div class="brand-disc"></div>
    <p class="brand-name">Fern Mentoring</p>
  </section>

  <section class="card card--back" aria-label="Card back">
    <div class="ray-field" role="img" aria-label="Soft sun ray decoration"></div>

    <div class="contact">
      <h1 class="contact__name">Greta Pellham</h1>
      <p class="contact__title">Business &amp; Personal Coach</p>
      <ul class="contact__list">
        <li class="contact__item">
          <svg class="contact__icon" viewBox="0 0 12 12"><path d="M3 1 L5 3.5 L4 5 Q5 7 7 8 L8.5 7 L11 9 L9.5 11 Q5 11 2.5 7.5 Q1 5 1.5 2.5 Z" fill="var(--sun)"/></svg>
          +61 (0)458 913307
        </li>
        <li class="contact__item">
          <svg class="contact__icon" viewBox="0 0 12 12"><rect x="0.5" y="2" width="11" height="8" rx="1.5" fill="var(--sun)"/><path d="M1 3 L6 7 L11 3" stroke="#fff" stroke-width="1" fill="none"/></svg>
          greta@fernmentoring-example.com.au
        </li>
        <li class="contact__item">
          <svg class="contact__icon" viewBox="0 0 12 12"><circle cx="6" cy="6" r="5.3" fill="var(--sun)"/><path d="M0.7 6 H11.3 M6 0.7 V11.3 M6 0.7 Q2.5 6 6 11.3 M6 0.7 Q9.5 6 6 11.3" stroke="#fff" stroke-width=".8" fill="none"/></svg>
          www.fernmentoring-example.com.au
        </li>
      </ul>
    </div>

    <p class="strapline">A<br>thinking partner<br>to<br>help you<br>cut through<br>the noise</p>

    <div class="social">
      <span class="social__mark"></span>
      @fernmentoringAU
    </div>
  </section>

</body>
</html>
```